Business Card Design for Occupational Medicine Start Up Company

We need to design a professional business card. We are a healthcare company providing occupational medicine services to blue collar industries. We are professional, efficient and high quality service providers.

Target Market(s)

Blue Collar Industry: Shipbuilding, Ports, Trucking Companies; The Executives and Safety Officers for these companies

Industry/Entity Type

Healthcare

Contact Information for Business Card

Logo, Name, Title, Email, Phone

Other font styles liked:
• Please match our Brand Guide

Requirements
Must have
• Our Company Colors and Logo

```html
<!DOCTYPE html>
<html lang="en">
<head>
<meta charset="utf-8">
<title>CrewWell Business Card</title>
<link href="https://fonts.googleapis.com/css2?family=Montserrat:wght@500;600&family=Poppins:wght@500;600;800&display=swap" rel="stylesheet">
<style>
  :root {
    --navy: #2b3080;
    --navy-deep: #161a48;
    --orange: #f2a944;
    --sky: #29a3dc;
    --white: #ffffff;
    --ink: #2a2a3a;
    --page: #f2f2f2;
  }
  * { margin: 0; padding: 0; box-sizing: border-box; }
  html, body { width: 800px; height: 1200px; overflow: hidden; }
  body {
    background: var(--page);
    font-family: "Poppins", sans-serif;
    position: relative;
  }
  .card {
    position: absolute;
    left: 80px;
    width: 640px;
    height: 366px;
    overflow: hidden;
    box-shadow: 0 4px 14px rgba(0,0,0,0.18);
  }
  .card-front { top: 214px; }
  .card-back { top: 620px; background: var(--white); }

  .navy-field {
    position: absolute;
    inset: 0;
    background: linear-gradient(180deg, var(--navy) 0%, #23286c 55%, var(--navy-deep) 100%);
  }
  .front-stripe {
    position: absolute;
    left: 0; right: 0; bottom: 0;
    height: 10px;
    background: var(--orange);
  }
  .front-brand {
    position: absolute;
    left: 0; right: 0; top: 112px;
    display: flex;
    flex-direction: column;
    align-items: center;
  }
  .brand-dot {
    width: 62px; height: 62px;
    border-radius: 50%;
    background: var(--orange);
  }
  .front-name {
    margin-top: 22px;
    font-family: "Montserrat", sans-serif;
    font-weight: 600;
    font-size: 35px;
    letter-spacing: 2px;
    color: var(--white);
  }
  .front-url {
    position: absolute;
    left: 0; right: 0; top: 290px;
    text-align: center;
    font-family: "Montserrat", sans-serif;
    font-weight: 600;
    font-size: 17px;
    letter-spacing: 2.5px;
    color: var(--white);
  }
  .front-url .accent { color: var(--orange); }

  .person {
    position: absolute;
    left: 51px; top: 72px;
  }
  .person-name {
    font-weight: 800;
    font-size: 32px;
    line-height: 1;
    letter-spacing: 0.5px;
    color: var(--navy);
  }
  .person-name .surname { color: var(--orange); }
  .person-title {
    margin-top: 7px;
    font-weight: 500;
    font-size: 13.5px;
    color: var(--ink);
  }
  .back-brand {
    position: absolute;
    left: 356px; top: 74px;
    display: flex;
    align-items: center;
    gap: 14px;
  }
  .back-brand .brand-dot { width: 44px; height: 44px; }
  .back-brand-name {
    font-family: "Montserrat", sans-serif;
    font-weight: 600;
    font-size: 20px;
    letter-spacing: 1px;
    color: var(--navy);
  }
  .accent-bars { position: absolute; left: 0; top: 0; }
  .back-field {
    position: absolute;
    left: 0; right: 0; top: 196px; bottom: 0;
    background: linear-gradient(180deg, var(--navy) 0%, #23286c 55%, var(--navy-deep) 100%);
  }
  .contact-list {
    position: absolute;
    top: 44px;
    list-style: none;
  }
  .contact-list.left { left: 50px; }
  .contact-list.right { left: 330px; }
  .contact-item {
    display: flex;
    align-items: center;
    gap: 10px;
    height: 27px;
    margin-bottom: 12px;
    font-weight: 500;
    font-size: 16.5px;
    color: var(--white);
  }
  .icon-badge {
    width: 26px; height: 26px;
    border-radius: 50%;
    background: var(--orange);
    display: flex; align-items: center; justify-content: center;
    flex: none;
  }
</style>
</head>
<body>

<section class="card card-front" aria-label="Card front">
  <div class="navy-field" role="img" aria-label="Navy gradient backdrop with a faint repeating brand pattern"></div>
  <div class="front-brand">
    <div class="brand-dot"></div>
    <div class="front-name">CREWWELL</div>
  </div>
  <p class="front-url">www.<span class="accent">crewwell</span>.com</p>
  <div class="front-stripe"></div>
</section>

<section class="card card-back" aria-label="Card back">
  <div class="person">
    <h1 class="person-name">DANA <span class="surname">REYES</span></h1>
    <p class="person-title">Executives and Safety Officers</p>
  </div>
  <div class="back-brand">
    <div class="brand-dot"></div>
    <span class="back-brand-name">CREWWELL</span>
  </div>

  <div class="back-field" role="img" aria-label="Navy gradient band with a faint repeating brand pattern">
    <ul class="contact-list left">
      <li class="contact-item">
        <span class="icon-badge">
          <svg width="14" height="14" viewBox="0 0 24 24" fill="none" stroke="#2b3080" stroke-width="2.4" stroke-linecap="round" stroke-linejoin="round"><path d="M22 16.9v3a2 2 0 0 1-2.2 2 19.8 19.8 0 0 1-8.6-3.1 19.5 19.5 0 0 1-6-6A19.8 19.8 0 0 1 2.1 4.2 2 2 0 0 1 4.1 2h3a2 2 0 0 1 2 1.7c.1.9.4 1.8.7 2.7a2 2 0 0 1-.5 2.1L8 9.8a16 16 0 0 0 6 6l1.3-1.3a2 2 0 0 1 2.1-.4c.9.3 1.8.6 2.7.7a2 2 0 0 1 1.7 2z"/></svg>
        </span>
        555.014.2287
      </li>
      <li class="contact-item">
        <span class="icon-badge">
          <svg width="14" height="14" viewBox="0 0 24 24"><path d="M12 2a7 7 0 0 0-7 7c0 5 7 13 7 13s7-8 7-13a7 7 0 0 0-7-7z" fill="#2b3080"/><circle cx="12" cy="9" r="2.6" fill="#f2a944"/></svg>
        </span>
        Harbor Road 45
      </li>
    </ul>
    <ul class="contact-list right">
      <li class="contact-item">
        <span class="icon-badge">
          <svg width="14" height="14" viewBox="0 0 24 24" fill="none" stroke="#2b3080" stroke-width="2.2" stroke-linejoin="round"><rect x="3" y="5" width="18" height="14" rx="1.5"/><path d="M3 6l9 7 9-7"/></svg>
        </span>
        hello@crewwell.com
      </li>
      <li class="contact-item">
        <span class="icon-badge">
          <svg width="15" height="15" viewBox="0 0 24 24" fill="none" stroke="#2b3080" stroke-width="2"><circle cx="12" cy="12" r="9"/><path d="M3 12h18M12 3c3 3 3 15 0 18M12 3c-3 3-3 15 0 18"/></svg>
        </span>
        www.crewwell.com
      </li>
    </ul>
  </div>

  <svg class="accent-bars" width="640" height="200" viewBox="0 0 640 200" aria-hidden="true">
    <rect x="200" y="181" width="245" height="6" rx="3" fill="#f2a944"/>
    <rect x="180" y="186" width="282" height="6" rx="3" fill="#2b3080"/>
    <rect x="155" y="190" width="331" height="6" rx="3" fill="#29a3dc"/>
  </svg>
</section>

</body>
</html>
```